KRT Engineering Business Card Design

We’re looking for an elegant, clean, and timeless business card design that communicates experience, capability, and reliability.

KRT Engineering was established in 1995 , we are a Government Contracting company providing Professional Services to the Office of Frontier Affairs, Harbor Protection and the Vantage Collective. Our capabilities include: Acquisition & Program Management; Intelligence & Security Operations; Cyber, IT & Network Operations; Lifecycle Logistics & Asset Readiness; C5ISR Systems Engineering & Sustainment.

We want the card to reflect a straightforward, confident approach to business. The design should feel polished and professional without being flashy or overly corporate.

Design Direction
Clean, sophisticated, and uncluttered
Elegant but understated
Strong typography and thoughtful spacing
A timeless aesthetic rather than something overly trendy
Confident and established, with a sense of substance
Easy to read and practical in a real-world business setting

The overall impression should be: “These are experienced professionals who know what they’re doing, do what they say, and can be relied upon.”

We’re open to creative interpretations. The finished card should feel distinctive through its typography, proportions, layout, and attention to detail rather than through excessive graphics or visual effects.

We’re looking for a design that would make a potential client immediately feel that they’re dealing with a capable, trustworthy, and established company.

Company Colors: Navy and Gold/Yellow (but you do not need to use these colors on the card)
Company Name: KRT Engineering Associates, Inc. (known as KRT Engineering)
Website: krtengineering.com
Company Logo: Navy & Gold (other variations attached)

```html
<!DOCTYPE html>
<html lang="en">
<head>
<meta charset="utf-8">
<title>KRT Engineering Business Card</title>
<link href="https://fonts.googleapis.com/css2?family=Lato:wght@400;700;900&display=swap" rel="stylesheet">
<style>
  :root {
    --navy: #1f2a5e;
    --navy-deep: #1b2354;
    --gold: #fde04c;
    --olive: #b3a74c;
    --white: #ffffff;
    --stage: #8e8e8e;
  }
  * { margin: 0; padding: 0; box-sizing: border-box; }
  html, body { width: 1200px; height: 1000px; overflow: hidden; }
  body { background: var(--stage); font-family: "Lato", sans-serif; position: relative; }

  .card {
    position: absolute;
    left: 290px;
    width: 629px;
    height: 359px;
    border-radius: 20px;
    overflow: hidden;
    box-shadow: 0 2px 4px rgba(0,0,0,0.25);
  }
  .card--front { top: 97px; background: var(--navy); }
  .card--back { top: 532px; }

  .front-shapes { position: absolute; inset: 0; width: 100%; height: 100%; }

  .hero-photo {
    position: absolute;
    right: 0; top: 0;
    width: 320px; height: 90px;
    background: radial-gradient(ellipse at 45% 55%, rgba(190,190,230,0.7) 0%, rgba(90,100,160,0.45) 35%, rgba(31,42,94,0) 75%);
  }

  .holder { position: absolute; left: 40px; top: 38px; }
  .holder__name { color: var(--gold); font-weight: 700; font-size: 27px; letter-spacing: 0.3px; line-height: 1; }
  .holder__title { color: var(--white); font-weight: 400; font-size: 15px; margin-top: 6px; }

  .brand-mark {
    position: absolute;
    left: 181px; top: 260px;
    transform: translate(-50%, -50%);
    color: var(--navy);
    font-weight: 900;
    font-size: 50px;
    letter-spacing: 1px;
  }

  .contact { position: absolute; left: 326px; top: 163px; color: var(--navy); font-size: 14.5px; line-height: 21.7px; letter-spacing: 0.3px; }
  .contact__company { font-weight: 700; }
  .contact__list { list-style: none; margin-top: 2px; }
  .contact__item { display: flex; align-items: center; gap: 9px; }
  .contact__icon { width: 11px; height: 11px; fill: var(--navy); flex: none; }

  .back-photo {
    position: absolute; inset: 0;
    background:
      radial-gradient(ellipse at 55% 35%, rgba(70,70,80,0.45) 0%, rgba(31,42,94,0) 60%),
      linear-gradient(160deg, var(--olive) 0%, #6b6a55 25%, #3a4064 50%, var(--navy) 72%, var(--navy-deep) 100%);
  }
  .back-mark {
    position: absolute;
    left: 315px; top: 199px;
    transform: translate(-50%, -50%);
    color: var(--white);
    font-weight: 900;
    font-size: 84px;
    letter-spacing: 2px;
  }
</style>
</head>
<body>

<section class="card card--front">
  <div class="hero-photo" role="img" aria-label="Photo of aircraft carrier deck lights at night"></div>
  <svg class="front-shapes" viewBox="0 0 1100 628" preserveAspectRatio="none" aria-hidden="true">
    <path fill="var(--gold)" d="M0,398 C250,270 450,160 720,143 C880,135 1020,170 1100,213 L1100,628 L0,628 Z"/>
    <path fill="var(--white)" d="M0,404 C300,262 520,212 700,212 C870,212 1000,270 1100,350 L1100,628 L0,628 Z"/>
  </svg>

  <div class="holder">
    <h1 class="holder__name">MARLA PENDLETON</h1>
    <p class="holder__title">President, CEO &amp; Founder</p>
  </div>

  <div class="brand-mark">KRT</div>

  <div class="contact">
    <p class="contact__company">KRT Engineering Associates, Inc</p>
    <p>4810 Harbor Crest Road, Suite 310</p>
    <p>Norfield, VA 23590</p>
    <ul class="contact__list">
      <li class="contact__item">
        <svg class="contact__icon" viewBox="0 0 24 24"><path d="M6.6 10.8a15.1 15.1 0 0 0 6.6 6.6l2.2-2.2c.3-.3.7-.4 1-.2 1.1.4 2.3.6 3.6.6.6 0 1 .4 1 1V20c0 .6-.4 1-1 1C10.6 21 3 13.4 3 4c0-.6.4-1 1-1h3.5c.6 0 1 .4 1 1 0 1.3.2 2.5.6 3.6.1.3 0 .7-.2 1z"/></svg>
        <span>555-204-3188</span>
      </li>
      <li class="contact__item">
        <svg class="contact__icon" viewBox="0 0 24 24"><path d="M7 1h10a2 2 0 0 1 2 2v18a2 2 0 0 1-2 2H7a2 2 0 0 1-2-2V3a2 2 0 0 1 2-2zm0 3v14h10V4zm5 15.5a1.2 1.2 0 1 0 0 2.4 1.2 1.2 0 0 0 0-2.4z"/></svg>
        <span>555-204-3188</span>
      </li>
      <li class="contact__item">
        <svg class="contact__icon" viewBox="0 0 24 24"><path d="M2 5h20v14H2zm2 2v.4l8 5.2 8-5.2V7zm0 2.8V17h16V9.8l-8 5.2z"/></svg>
        <span>info@krtengineering.com</span>
      </li>
      <li class="contact__item">
        <svg class="contact__icon" viewBox="0 0 24 24"><path d="M12 2a10 10 0 1 0 0 20 10 10 0 0 0 0-20zm0 2.2a7.8 7.8 0 0 1 7.4 5.3H16c-.4-1.8-1.2-3.4-2.2-4.8.1 0-1.2-.5-1.8-.5zM4.6 14.5h3.6c.3 1.9 1 3.5 2 4.9a7.8 7.8 0 0 1-5.6-4.9zm0-5h3.6c.3-1.9 1-3.5 2-4.9a7.8 7.8 0 0 0-5.6 4.9zm5.8 0c.4-2 1-3.5 1.6-4.5.6 1 1.2 2.5 1.6 4.5zm0 5h3.2c-.4 2-1 3.5-1.6 4.5-.6-1-1.2-2.5-1.6-4.5zm5.6 0h3.4a7.8 7.8 0 0 1-5.4 4.9c1-1.4 1.7-3 2-4.9zM10.2 11.7h3.6v.6h-3.6z"/></svg>
        <span>krtengineering.com</span>
      </li>
    </ul>
  </div>
</section>

<section class="card card--back">
  <div class="back-photo" role="img" aria-label="Photo of a fighter jet in flight, tinted gold to navy"></div>
  <div class="back-mark">KRT</div>
</section>

</body>
</html>
```